Business card for event manager / organizer "waiter service"

Draft of a new valuable business card for my company.
Events, personnel service providers, festivals

```html
<!DOCTYPE html>
<html lang="de">
<head>
<meta charset="utf-8">
<title>Nordlicht Servicecrew – Visitenkarte</title>
<link href="https://fonts.googleapis.com/css2?family=Poppins:wght@300;400;500;600;700&display=swap" rel="stylesheet">
<style>
  :root {
    --stage: #3a3a3c;
    --card: #1d1d1d;
    --orange: #f08a24;
    --orange-deep: #8a3a12;
    --white: #ffffff;
    --muted: #d9d9d9;
  }
  * { box-sizing: border-box; margin: 0; padding: 0; }
  html, body { width: 1200px; height: 900px; overflow: hidden; }
  body {
    background: var(--stage);
    font-family: "Poppins", sans-serif;
    position: relative;
  }
  .card {
    position: absolute;
    left: 280px;
    width: 640px;
    height: 370px;
    background: var(--card);
    border-radius: 22px;
    overflow: hidden;
    box-shadow: 0 10px 30px rgba(0,0,0,.45);
  }
  .card--front { top: 50px; }
  .card--back { top: 470px; }

  .brand {
    position: absolute;
    display: flex;
    align-items: center;
  }
  .card--front .brand { left: 70px; top: 105px; gap: 28px; }
  .brand__mark {
    background: linear-gradient(135deg, var(--orange), var(--orange-deep));
    flex: none;
  }
  .card--front .brand__mark { width: 130px; height: 130px; }
  .brand__text { display: flex; flex-direction: column; }
  .brand__name {
    color: var(--white);
    font-weight: 700;
    text-transform: uppercase;
    line-height: 1.05;
  }
  .card--front .brand__name { font-size: 40px; }
  .brand__tagline {
    color: var(--muted);
    font-weight: 300;
    margin-top: 8px;
  }
  .card--front .brand__tagline { font-size: 17px; }

  .card--back .brand { left: 34px; top: 30px; gap: 12px; }
  .card--back .brand__mark { width: 52px; height: 52px; }
  .card--back .brand__name { font-size: 16px; }
  .card--back .brand__tagline { font-size: 8px; margin-top: 3px; }

  .person {
    position: absolute;
    left: 34px;
    top: 118px;
  }
  .person__name {
    color: var(--orange);
    font-weight: 600;
    font-size: 30px;
    line-height: 1.1;
  }
  .person__role {
    color: var(--white);
    font-weight: 300;
    font-size: 15px;
    margin-top: 2px;
    margin-left: 20px;
  }
  .contact {
    position: absolute;
    left: 54px;
    top: 206px;
    list-style: none;
  }
  .contact__item {
    display: flex;
    align-items: center;
    gap: 10px;
    color: var(--white);
    font-size: 14.5px;
    line-height: 24px;
  }
  .contact__icon { width: 14px; height: 14px; flex: none; }
  .contact__icon--square { background: var(--orange); border-radius: 2px; }

  .portrait {
    position: absolute;
    right: 0;
    top: 30px;
    width: 270px;
    height: 310px;
    border-radius: 140px 0 0 120px;
    background: radial-gradient(ellipse at 55% 40%, #9a9a9e 0%, #55555a 45%, #262628 80%);
  }
</style>
</head>
<body>

<section class="card card--front">
  <div class="brand">
    <div class="brand__mark"></div>
    <div class="brand__text">
      <span class="brand__name">Nordlicht<br>Servicecrew</span>
      <span class="brand__tagline">…weil jedes Fest gute Hände braucht!</span>
    </div>
  </div>
</section>

<section class="card card--back">
  <div class="brand">
    <div class="brand__mark"></div>
    <div class="brand__text">
      <span class="brand__name">Nordlicht<br>Servicecrew</span>
      <span class="brand__tagline">…weil jedes Fest gute Hände braucht!</span>
    </div>
  </div>

  <div class="person">
    <p class="person__name">Jonas Brückner</p>
    <p class="person__role">Inhaber</p>
  </div>

  <ul class="contact">
    <li class="contact__item">
      <svg class="contact__icon" viewBox="0 0 24 24"><path fill="#f08a24" d="M6.6 10.8a15 15 0 0 0 6.6 6.6l2.2-2.2c.3-.3.7-.4 1-.2 1.1.4 2.3.6 3.6.6.6 0 1 .4 1 1V20c0 .6-.4 1-1 1A17 17 0 0 1 3 4c0-.6.4-1 1-1h3.5c.6 0 1 .4 1 1 0 1.3.2 2.5.6 3.6.1.3 0 .7-.2 1z"/></svg>
      02368 512 40 73
    </li>
    <li class="contact__item">
      <svg class="contact__icon" viewBox="0 0 24 24"><path fill="#f08a24" d="M6.6 10.8a15 15 0 0 0 6.6 6.6l2.2-2.2c.3-.3.7-.4 1-.2 1.1.4 2.3.6 3.6.6.6 0 1 .4 1 1V20c0 .6-.4 1-1 1A17 17 0 0 1 3 4c0-.6.4-1 1-1h3.5c.6 0 1 .4 1 1 0 1.3.2 2.5.6 3.6.1.3 0 .7-.2 1z"/></svg>
      0176 482 31 09
    </li>
    <li class="contact__item">
      <svg class="contact__icon" viewBox="0 0 24 24"><circle cx="12" cy="12" r="9" fill="none" stroke="#f08a24" stroke-width="2.5"/><path d="M3 12h18M12 3c3 3 3 15 0 18M12 3c-3 3-3 15 0 18" fill="none" stroke="#f08a24" stroke-width="2"/></svg>
      www.nordlicht-servicecrew.de
    </li>
    <li class="contact__item">
      <svg class="contact__icon" viewBox="0 0 24 24"><rect x="2" y="5" width="20" height="14" rx="2" fill="#f08a24"/><path d="M3 6l9 7 9-7" fill="none" stroke="#1d1d1d" stroke-width="2"/></svg>
      info@nordlicht-servicecrew.de
    </li>
    <li class="contact__item">
      <svg class="contact__icon" viewBox="0 0 24 24"><path fill="#f08a24" d="M12 2a7 7 0 0 0-7 7c0 5 7 13 7 13s7-8 7-13a7 7 0 0 0-7-7zm0 9.5A2.5 2.5 0 1 1 12 6.5a2.5 2.5 0 0 1 0 5z"/></svg>
      Birkenweg 12, 45700 Musterstadt
    </li>
    <li class="contact__item">
      <span class="contact__icon contact__icon--square"></span>
      social: /nordlichtcrew
    </li>
  </ul>

  <div class="portrait" role="img" aria-label="Portraitfoto des Inhabers in weißem Hemd und schwarzer Weste mit verschränkten Armen"></div>
</section>

</body>
</html>
```